BLUE & ORANGE BALM TOPICAL BOX + LABELS TO MATCH

Hello ! I hope you're up to helping with my designs again. I appreciate all your help.
I have two topicals needing redesign.
Box + Label , once the box is together, we can slap the labels together easy.
I have CBD version and THC version of both these balms, so well start w THC, then lay out the CBD. It should be eaay with few minor differences.
PLEASE USE only tHE SMALL BOX TEMPLATE,
Anyway, once the boxes are complete, I need to revise the label to match the boxes.
1.
ORANGE BALM :
(this box color I would like orange, like a jack-o-lantern (i uploaded our current label so you can match it)
KORVEN logo outlined in Gold (on LID)
(I uploaded a picture of what the oulined logo looks like)
THC SYMBOL
ORANGE BALM (GOLD) (on Front)
HIGHLY NUTRITIOUS POWERFUL THC RELIEF
net wt. 2 oz (56 g)
SIDE PANEL :
ORGANIC INGREDIENTS : Butyrospermum Parkii Butter (Shea Butter), Persia Gratissima (Avocado) Oil, Simmondsia chinesis (Gold Jojoba) Oil , Vitus Vinifera (Grape) Seed Oil, Arnica montana (Arnica) and Symphytum officinalis (Comfrey Leaf) macerated in Sunflower Oil, Calophyllum inophyllum (Tamanu) Oil, Nigella sativa (Black Seed) Oil, Locally Harvested Beeswax, THC CANNABIS EXTRACT, Pure Cannabigerol (CBG), Proprietary Blend of Therapeutic Essential Oils (including but not limited to : Yarrow , Celery Seed , Tea Tree , Lavender , Helichrysum, Pine Scotch, Rosemary, Geranium), Tocopherol (Vitamin E, antioxidant )
Color is a Natural Result of Chamomile Steam-Distillation and May Vary in Intensity. Consistency can also Vary. For Optimal Preservation, Keep in a Cool, Dark Place. Fatty Acids may Naturally Aggregate when Exposed to Temperature Extremes Forming Beads. To Fix This, Use a Hair Dryer to Melt them Back to a Smooth Consistency.
BACK PANEL :
WARNING: THIS PRODUCT IS FOR USE BY INDIVIDUALS 21 YEARS OF AGE OR OLDER OR BY REGISTERED QUALIFYING PATIENTS ONLY. IT IS ILLEGAL TO DRIVE A MOTOR VEHICLE WHILE UNDER THE INFLUENCE OF MARIJUANA.
(Outlined Box )::
WARNING: USE BY PREGNANT OR BREASTFEEDING WOMEN OR BY WOMEN PLANNING TO BECOME PREGNANT, MAY RESULT IN FETAL INJURY, PRETERM BIRTH, LOW BIRTHWEIGHT, OR DEVELOPMENTAL PROBLEMS FOR THE CHILD.
KEEP OUT OF REACH OF CHILDREN.
CENTRAL TOXIN RESPONSE BUREAU 1 800 555 0147
THE ACTUAL VALUE OF CANNABINOIDS MAY VARY FROM THE REPORTED VALUE BY +/- 10%
ACTIVATION TIME : 10 - 60 MINUTES
MADE IN A MARIJUANA FACILITY
PACKAGED BY
MIRABEL’S LUSH Co.
QX-R-748315
www.LUSHTARTS.info
2.
BLUE BALM
white box
KORVEN Gold out line, red w blue leaf
FRONT PANEL :
BLUE BALM (blue)
net wt. 2 oz (56 g)
Ingredients : Butyrospermum Parkii Butter (Shea Butter), Aloe Barbadensis (Aloe Vera) Leaf Extract, Coco Nucifera (Coconut) Oil, THC CANNABIS EXTRACT, Cannabis Sativa Seed Oil, Pure Cannabidol (Hemp Extract), Prunes Armeniaca (Apricot) Kernal Oil, Hydrogenated Vegetable (Soybean) Oil, Prunus Amygdalus Dulcis (Sweet Almond Oil), Vitus Vinifera (Grape) Seed Oil, Macadamia Ternifolia Seed Oil, Daucus Carota (Carrot) Seed Oil, Proprietary Blend of Therapeutic Essential Oils (including but not limited to : Lavender, Chamomile), Tocopherol (Vitamin E, antioxidant)

```html
<!DOCTYPE html>
<html lang="en">
<head>
<meta charset="utf-8">
<title>Korven Botanic Orange Balm – Box Dieline</title>
<link rel="stylesheet" href="https://fonts.googleapis.com/css2?family=Chango&family=Bebas+Neue&family=Montserrat:wght@500&family=Roboto+Condensed:wght@300;400;700&display=swap">
<style>
  :root{
    --box-orange:#f06a22;
    --gold:#fcc02b;
    --brand-red:#e42a2a;
    --leaf-green:#8cc63f;
    --cut:#1a1a1a;
    --fold:#8bc34a;
    --paper:#ffffff;
  }
  html,body{margin:0;padding:0;background:var(--paper);overflow:hidden;}
  .canvas{position:relative;width:1200px;height:992px;overflow:hidden;background:var(--paper);}
  .dieline{position:absolute;left:0;top:0;}
  .bleed{fill:var(--box-orange);}
  .cut{fill:none;stroke:var(--cut);stroke-width:.6;}
  .fold{fill:none;stroke:var(--fold);stroke-width:.5;}

  .brand{position:absolute;left:298px;width:266px;text-align:center;margin:0;
    font-family:"Chango",cursive;font-size:44px;line-height:1;color:var(--brand-red);}
  .sub{position:absolute;left:298px;width:266px;text-align:center;margin:0;
    font-family:"Montserrat",sans-serif;font-weight:500;font-size:15px;letter-spacing:9px;
    text-indent:9px;color:var(--gold);}
  .product{position:absolute;left:298px;width:266px;text-align:center;margin:0;
    font-family:"Bebas Neue",sans-serif;font-size:60px;line-height:1;letter-spacing:-.5px;color:var(--gold);}
  .netwt{position:absolute;left:298px;width:266px;top:578px;text-align:center;margin:0;
    font-family:"Roboto Condensed",sans-serif;font-weight:700;font-size:9.5px;color:var(--gold);}

  .copy{position:absolute;margin:0;font-family:"Roboto Condensed",sans-serif;font-weight:300;color:var(--gold);}
  .uses{left:55px;width:226px;top:471px;font-size:10px;line-height:14px;letter-spacing:-.15px;text-align:justify;}
  .uses p{margin:0 0 11px;}
  .uses .one-line{white-space:nowrap;text-align:left;}
  .ingredients{left:583px;width:226px;top:401px;font-size:8.6px;line-height:10.5px;text-align:justify;}
  .ingredients p{margin:0 0 9px;}
  .ingredients .care{font-size:6.9px;line-height:10.4px;}

  .back{left:848px;width:226px;top:401px;text-align:center;font-weight:400;text-transform:uppercase;}
  .back p{margin:0;}
  .back .claims{font-weight:700;font-size:9.8px;line-height:12px;margin-bottom:2px;white-space:nowrap;}
  .back .small{font-size:7.5px;line-height:8.8px;}
  .back .gap{margin-top:5px;}
  .back .warning-box{border:1px solid var(--gold);padding:2px 5px;margin:8px 0 7px;font-size:7.4px;line-height:8.7px;text-align:justify;text-align-last:center;}
  .back .fda{text-transform:none;font-weight:300;font-size:6.9px;line-height:8px;margin-top:6px;}
</style>
</head>
<body>
<div class="canvas">
  <svg class="dieline" width="1200" height="992" viewBox="0 0 1200 992">
    <g class="bleed">
      <path d="M287 119 V70 A49 49 0 0 1 336 21 H526 A49 49 0 0 1 575 70 V119 Z"/>
      <rect x="285" y="105" width="293" height="285"/>
      <polygon points="23,346 37,331 62,242 285,242 285,390 23,390"/>
      <polygon points="577,242 800,242 825,331 840,347 840,390 564,390 564,300"/>
      <polygon points="23,346 840,346 840,371 1095,371 1177,393 1177,597 1107,614 23,614 23,346"/>
      <polygon points="23,600 298,600 310,620 310,643 294,658 270,748 38,748 35,621 23,606"/>
      <polygon points="553,600 814,600 814,748 591,748 567,657 553,643"/>
      <rect x="814" y="600" width="293" height="285"/>
      <path d="M817 870 V920 A49 49 0 0 0 866 969 H1056 A49 49 0 0 0 1105 920 V870 Z"/>
    </g>
    <g class="cut">
      <path d="M301 119 V85 A50 50 0 0 1 351 35 H511 A50 50 0 0 1 561 85 V119"/>
      <path d="M298 386 V119 H336 V123 M526 123 V119 H564 V386"/>
      <polyline points="36,386 36,353 50,339 72,255 280,255 284,374 294,386"/>
      <polyline points="576,374 582,255 790,255 811,339 826,353 826,386"/>
      <polyline points="36,386 36,604 47,617 51,734 260,734 282,650 296,636 296,604"/>
      <polyline points="566,604 566,636 580,650 602,734 810,734 814,618 829,604"/>
      <polyline points="1093,386 1163,404 1163,586 1093,604"/>
      <path d="M829 604 V870 H866 V866 M1056 866 V870 H1093 V604"/>
      <path d="M830 870 V904 A50 50 0 0 0 880 954 H1041 A50 50 0 0 0 1091 904 V870"/>
    </g>
    <g class="fold">
      <line x1="36" y1="386" x2="1093" y2="386"/>
      <line x1="36" y1="604" x2="1093" y2="604"/>
      <line x1="298" y1="386" x2="298" y2="604"/>
      <line x1="564" y1="386" x2="564" y2="604"/>
      <line x1="829" y1="386" x2="829" y2="604"/>
      <line x1="1093" y1="386" x2="1093" y2="604"/>
      <line x1="336" y1="123" x2="526" y2="123"/>
      <line x1="866" y1="866" x2="1056" y2="866"/>
    </g>

    <!-- compliance mark placeholder -->
    <circle class="compliance-spot" cx="525" cy="414" r="18" fill="none" stroke="var(--gold)" stroke-width="1.2"/>

    <defs>
      <path id="arc-top-1" d="M58 430 A21 21 0 0 1 100 430"/>
      <path id="arc-bot-1" d="M58 430 A21 21 0 0 0 100 430"/>
      <path id="arc-top-2" d="M117 430 A21 21 0 0 1 159 430"/>
      <path id="arc-bot-2" d="M117 430 A21 21 0 0 0 159 430"/>
      <path id="arc-top-3" d="M176 430 A21 21 0 0 1 218 430"/>
      <path id="arc-bot-3" d="M176 430 A21 21 0 0 0 218 430"/>
      <path id="arc-top-4" d="M234 430 A21 21 0 0 1 276 430"/>
      <path id="arc-bot-4" d="M234 430 A21 21 0 0 0 276 430"/>
    </defs>
    <g class="icons" fill="none" stroke="var(--gold)" stroke-width=".9">
      <circle cx="79" cy="430" r="23.5"/>
      <circle cx="138" cy="430" r="23.5"/>
      <circle cx="197" cy="430" r="23.5"/>
      <circle cx="255" cy="430" r="23.5"/>
      <path d="M72 440 C70 428 76 420 86 418 C88 430 82 438 72 440 Z" fill="var(--leaf-green)"/>
      <path d="M140 420 L133 432 H139 L136 441 L144 428 H138 Z" fill="var(--leaf-green)"/>
      <circle cx="197" cy="430" r="7"/>
      <path d="M247 438 Q255 442 264 434 M255 426 q-3 -5 0 -8 q3 3 0 8"/>
    </g>
    <g class="icon-labels" font-family="Roboto Condensed, sans-serif" font-size="7" fill="var(--gold)"
       stroke="var(--box-orange)" stroke-width="3" paint-order="stroke" letter-spacing="1.2" text-anchor="middle">
      <text><textPath href="#arc-top-1" startOffset="50%">ORGANIC</textPath></text>
      <text dominant-baseline="hanging"><textPath href="#arc-bot-1" startOffset="50%">INGREDIENTS</textPath></text>
      <text><textPath href="#arc-top-2" startOffset="50%">HIGH</textPath></text>
      <text dominant-baseline="hanging"><textPath href="#arc-bot-2" startOffset="50%">POTENCY</textPath></text>
      <text><textPath href="#arc-top-3" startOffset="50%">POWERFUL</textPath></text>
      <text dominant-baseline="hanging"><textPath href="#arc-bot-3" startOffset="50%">RELIEF</textPath></text>
      <text><textPath href="#arc-top-4" startOffset="50%">NATURAL</textPath></text>
      <text dominant-baseline="hanging"><textPath href="#arc-bot-4" startOffset="50%">HEALING</textPath></text>
    </g>
  </svg>

  <p class="brand" style="top:192px">KORVEN</p>
  <p class="sub" style="top:247px">BOTANIC</p>
  <p class="product" style="top:268px">ORANGE BALM</p>

  <p class="brand" style="top:444px">KORVEN</p>
  <p class="sub" style="top:499px">BOTANIC</p>
  <p class="product" style="top:520px">ORANGE BALM</p>
  <p class="netwt">net wt. 2 oz (56 g)</p>

  <div class="copy uses">
    <p class="one-line">USES: Potent Relief with Healing. Suitable for All Skin Types.</p>
    <p>FORMULA: Organic. Contains THC. Potent anti-inflam-matory providing dominate relief. High Phytonutrient content with powerful healing properties.</p>
    <p>HOW TO USE: Apply Generously onto skin and massage until absorbed. For maximum effect use daily, mornings and evenings, and as needed for deep relief.</p>
  </div>

  <div class="copy ingredients">
    <p>ORGANIC INGREDIENTS : Butyrospermum Parkii Butter (Shea Butter), Persia Gratissima (Avocado) Oil, Simmondsia chinesis (Gold Jojoba) Oil, Vitus Vinifera (Grape) Seed Oil, Arnica montana (Arnica) and Symphytum officinalis (Comfrey Leaf) macerated in Sunflower Oil, Calophyllum inophyllum (Tamanu) Oil, Nigella sativa (Black Seed) Oil, Locally Harvested Beeswax, THC CANNABIS EXTRACT, Pure Cannabigerol (CBG), Proprietary Blend of Therapeutic Essential Oils (including but not limited to : Yarrow, Celery Seed, Tea Tree, Lavender, Helichrysum, Pine Scotch, Rosemary, Geranium), Tocopherol (Vitamin E, antioxidant )</p>
    <p class="care">Color is a Natural result of the Phytonutrients within the Formula and May Vary in Intensity. Consistency may also Vary. For Optimal Preservation, Keep in a Cool, Dark Place. Fatty Acids may Naturally Aggregate when Exposed to Temperature Extremes Forming Beads. To Fix This, Use a Hair Dryer to Melt them Back to a Smooth Consistency. For Best Results, Apply to Skin after a warm wash. Botanical oils and Healing compounds are better able to lock into the dermis when the pores are clean, warm and open.</p>
  </div>

  <div class="copy back">
    <p class="claims">POTENT RELIEF • ULTRA HEALING NON PSYCHOACTIVE<br>• SMALL BATCH PLANT BASED • HIGH THC FORMULA</p>
    <p class="small" style="text-align:justify;text-align-last:center">ACTIVATION TIME : THIS PRODUCT IS FOR USE BY INDIVIDUALS 21 YEARS OF AGE OR OLDER OR BY REGISTERED QUALIFYING PATIENTS ONLY. IT IS ILLEGAL TO DRIVE A MOTOR VEHICLE WHILE UNDER THE INFLUENCE OF MARIJUANA. ACTIVATION TIME : 30 MINUTES.</p>
    <p class="small gap">KEEP OUT OF REACH OF CHILDREN.<br>CENTRAL TOXIN RESPONSE BUREAU 1 800 555 0147</p>
    <p class="warning-box">WARNING: USE BY PREGNANT OR BREASTFEEDING WOMEN OR BY WOMEN PLANNING TO BECOME PREGNANT, MAY RESULT IN FETAL INJURY, PRETERM BIRTH, LOW BIRTHWEIGHT, OR DEVELOPMENTAL PROBLEMS FOR THE CHILD.</p>
    <p class="small">THE ACTUAL VALUE OF CANNABINOIDS MAY<br>VARY FROM THE REPORTED VALUE BY +/-10%<br>MADE IN A MARIJUANA FACILITY<br>PACKAGED BY : MIRABEL’S LUSH QX-R-748315</p>
    <p class="fda">These Statements have not been evaluated by the FDA. This product is not intended to diagnose, treat, cure, or prevent any disease or condition.</p>
  </div>
</div>
</body>
</html>
```